Distribution/Printing company needs a web site to inform prospective customers on what we do.

Distribution/Printing/Packaging company needs a web site to inform prospective customers on what we do. Please look at our direct to consumer web site (under development) for an idea of the product lines we sell: storedev.maplewickhaven.com
Logo files are attached as is a flyer that is under development which contains other information about the company (this is to be used for content- not to be posted as is). The web site should be focused on our business customer base and is not intended to be direct to consumer. Site should have a link to our consumer web site.
Site design should be mobile friendly, or mobile could be redirected to a mobile version. This web site will be strictly informational and will not be designed for any sales transactions.

Target Market(s)

Manufacturing and retail businesses, any other multi-site business that would benefit from centralized pricing and budget controls we can provide (banks, medical/dental offices, educational facilities, etc).

Industry/Entity Type

It Company

Coding

Coded - Design and coding required

Number of Pages Required

5+ page

Requirements
Must have
• 1) Top level menu: Products, about us, locations, contact us, news
• 2) page with news/promotions that is easily updated
• 3) "contact us" form (name, company, phone, email address) email link
• 4) link to www.store.maplewickhaven.com with information that lower pricing is available for businesses
• 5) SEO keywords
• 6) Link to powerpoint presentation file
Nice to have
• 1) our phone number should appear on every page near the top

```html
<!DOCTYPE html>
<html lang="en">
<head>
<meta charset="utf-8">
<title>Maplewick Haven Supply — Packaging, Printing, Distribution for Business</title>
<meta name="keywords" content="business packaging supplies, commercial printing, distribution, office supplies, janitorial supplies, retail supplies, centralized purchasing, multi-site budget control">
<link href="https://fonts.googleapis.com/css2?family=Open+Sans:wght@400;600;700&family=Arimo:wght@400;700&display=swap" rel="stylesheet">
<style>
:root{
  --ink-dark:#1c1c1c;
  --nav-line:#b9b9b9;
  --page-light:#f1f1f1;
  --panel-grey:#e6e6e6;
  --orange:#c9480f;
  --orange-deep:#a8360a;
  --link-rust:#b05a35;
  --link-green:#6f8d12;
  --text-grey:#6a6a6a;
  --text-dim:#8a8a8a;
  --white:#ffffff;
}
*{box-sizing:border-box;margin:0;padding:0}
html,body{width:1007px;height:1200px;overflow:hidden}
body{position:relative;background:var(--page-light);font-family:"Arimo",Arial,sans-serif;color:var(--text-grey)}
a{color:inherit}
.abs{position:absolute}

/* header */
.site-header{left:0;top:0;width:1007px;height:98px;background:radial-gradient(ellipse at 30% 40%,#3a3a3a,var(--ink-dark) 70%)}
.brand{left:107px;top:48px;color:var(--white)}
.brand-name{display:flex;align-items:center;gap:8px;font-family:"Open Sans",sans-serif;font-weight:700;font-size:16px;letter-spacing:.3px}
.brand-square{width:10px;height:10px;background:var(--white)}
.brand-tagline{font-family:"Open Sans",sans-serif;font-weight:600;font-size:10.5px;margin-top:6px;padding-left:4px}
.search{left:705px;top:37px;display:flex}
.search-field{width:169px;height:25px;background:#0b0b0b;color:#ddd;font-size:12px;padding:6px 8px}
.search-btn{width:25px;height:25px;background:#3c3c3c}
.phone{left:705px;top:70px;width:194px;display:flex;align-items:center;justify-content:flex-end;gap:6px;font-size:12px;color:#ddd}
.phone strong{color:var(--white);font-weight:700}

/* nav */
.main-nav{left:0;top:98px;width:1007px;height:40px;background:linear-gradient(#f3f3f3,#d3d3d3);border-top:1px solid #fff}
.nav-list{position:absolute;left:107px;top:0;display:flex;list-style:none;height:40px}
.nav-list li{height:40px;line-height:40px;padding:0 20px;font-size:15px;color:#222;border-right:1px solid var(--nav-line)}
.nav-list li.is-active{background:#2b2b2b;color:var(--white);border-right:none}

/* hero */
.hero{left:0;top:138px;width:1007px;height:315px;background:radial-gradient(ellipse at 50% 30%,#393939,#1d1d1d 80%)}
.service-tile{left:107px;width:239px;height:97px;padding:16px 21px 0}
.service-tile h2{display:flex;align-items:center;gap:6px;font-family:"Arimo",Arial,sans-serif;font-weight:400;font-size:23px;color:var(--white);line-height:24px}
.tile-arrow{width:14px;height:14px}
.service-tile p{font-family:"Open Sans",sans-serif;font-weight:700;font-size:10.5px;color:var(--white);margin:4px 0 8px}
.btn-small{display:inline-block;font-size:10px;padding:3px 5px;border-radius:2px}
.btn-light{background:var(--white);color:#222}
.btn-dark{background:#222;color:#eee}
.tile-packaging{top:148px;background:linear-gradient(var(--orange),var(--orange-deep))}
.tile-printing{top:248px;background:linear-gradient(#f0b418,#d68e06)}
.tile-distribution{top:347px;background:linear-gradient(#9cc028,#7c9e14)}
.hero-media{left:350px;top:148px;width:550px;height:297px;background:linear-gradient(100deg,#b48a5c 0%,#a27650 45%,#6a5a4c 70%,#8a7a6c 100%)}
.play-btn{left:816px;top:405px;width:62px;height:26px;background:linear-gradient(#fff,#ddd);border-radius:2px;color:#222;font-size:12px;text-align:center;line-height:26px}

/* capabilities */
.capabilities{left:107px;top:467px;width:239px;height:294px;background:var(--panel-grey)}
.panel-title{height:42px;background:linear-gradient(#3a3a3a,#1f1f1f);color:var(--white);font-family:"Open Sans",sans-serif;font-size:16px;line-height:42px;padding-left:21px}
.cap-list{list-style:none;padding:18px 20px 0 21px}
.cap-item{position:relative;padding-left:19px;margin-bottom:14px}
.cap-item::before{content:"";position:absolute;left:0;top:2px;width:10px;height:12px;border:1px solid #999;background:#f7f7f7}
.cap-item a{font-size:10.5px;color:var(--link-rust)}
.cap-item p{font-size:10px;line-height:15px;margin-top:4px;color:var(--text-grey)}

/* newsletter */
.newsletter{left:107px;top:770px;width:239px;height:125px;background:linear-gradient(var(--orange),var(--orange-deep));padding:18px 21px}
.newsletter h3{font-family:"Open Sans",sans-serif;font-weight:400;font-size:16px;color:var(--white)}
.newsletter-field{width:197px;height:20px;background:#e5e5e5;margin-top:12px;border:1px solid #bbb}
.newsletter-actions{display:flex;justify-content:space-between;align-items:center;margin-top:10px}
.btn-subscribe{background:var(--white);color:#111;font-size:12px;padding:6px 6px;border-radius:3px}
.unsubscribe{font-size:12px;color:var(--white)}

/* main content */
.section-title{font-family:"Open Sans",sans-serif;font-weight:400;font-size:20px;color:#333}
.intro-title{left:380px;top:481px}
.feature{left:380px;width:520px;display:flex;gap:19px}
.feature-media{width:158px;height:89px;border:1px solid #aaa;flex:none}
.media-office{background:linear-gradient(#b9c6d0,#dde2e4 45%,#cfcfcf)}
.media-boxes{background:linear-gradient(#8b7763,#c39058 40%,#d49a5a 80%,#9a8a7a)}
.feature h4{font-size:11px;font-weight:700;color:var(--link-green);text-decoration:underline;margin-top:8px}
.feature p{font-size:10.5px;line-height:15px;margin-top:9px;color:var(--text-grey)}
.feature-one{top:529px}
.feature-two{top:633px}
.lines-title{left:380px;top:773px}
.link-col{list-style:none;width:180px;font-size:10px;color:var(--link-rust)}
.link-col li{height:21px;padding-left:10px;position:relative}
.link-col li::before{content:"»";position:absolute;left:0;top:-1px}
.link-col a{text-decoration:underline}
.col-a{left:380px;top:818px}.col-b{left:565px;top:818px}.col-c{left:749px;top:818px}

/* footer */
.site-footer{left:0;top:921px;width:1007px;height:217px;background:radial-gradient(ellipse at 50% 20%,#343434,#1c1c1c 80%)}
.footer-col{top:949px;width:222px}
.footer-col h3{font-family:"Open Sans",sans-serif;font-weight:400;font-size:18px;color:var(--white);padding-bottom:10px;border-bottom:1px solid #3a3a3a}
.footer-services{left:128px}
.footer-standards{left:393px}
.footer-social{left:658px}
.service-list{list-style:none;font-size:10px;color:var(--text-dim);margin-top:6px}
.service-list li{height:24px;line-height:24px;border-bottom:1px solid #2e2e2e}
.service-list li::before{content:"» "}
.standards-lead{font-size:10.5px;font-weight:700;color:#9a9a9a;margin-top:14px}
.standards-text{font-size:10px;line-height:15px;color:var(--text-dim);margin-top:8px}
.btn-read{display:inline-block;margin-top:12px;background:var(--white);color:#111;font-size:12px;padding:6px 7px;border-radius:3px}
.social-list{list-style:none;margin-top:4px}
.social-list li{display:flex;justify-content:space-between;align-items:center;height:33px;border-bottom:1px solid #3a3a3a;font-size:8px;letter-spacing:.6px;color:#9a9a9a}
.social-square{width:18px;height:18px;border-radius:3px;margin-right:18px}
.sq-orange{background:#e0701d}.sq-blue{background:#3a9fd6}.sq-green{background:#2f9c4a}

.bottom-bar{left:0;top:1138px;width:1007px;height:62px;background:#141414;border-top:1px solid #2c2c2c}
.copyright{left:104px;top:1165px;font-size:9.5px;color:#777}
.footer-nav{left:433px;top:1165px;display:flex;list-style:none;font-size:9.5px;color:#777}
.footer-nav li+li::before{content:"|";margin:0 8px;color:#555}
.footer-nav .is-active{color:#ddd;text-decoration:underline}
</style>
</head>
<body>

<header class="site-header abs">
  <div class="brand abs">
    <div class="brand-name"><span class="brand-square"></span>MAPLEWICK HAVEN SUPPLY</div>
    <div class="brand-tagline">Packaging • Printing • Distribution</div>
  </div>
  <div class="search abs">
    <div class="search-field">Searching...</div>
    <div class="search-btn">
      <svg width="25" height="25" viewBox="0 0 25 25"><circle cx="11" cy="11" r="5" fill="none" stroke="#fff" stroke-width="2.2"/><line x1="15" y1="15" x2="19" y2="19" stroke="#fff" stroke-width="2.6" stroke-linecap="round"/></svg>
    </div>
  </div>
  <div class="phone abs">
    <svg width="12" height="12" viewBox="0 0 12 12"><path d="M2.5 1l2 2.2-1 1.3a7 7 0 0 0 4 4l1.3-1 2.2 2-1.2 1.5C5.5 11 1 6.5 1 2.2z" fill="#fff"/></svg>
    Call us: <strong>(555) 014-2276</strong>
  </div>
</header>

<nav class="main-nav abs">
  <ul class="nav-list">
    <li class="is-active">Home</li>
    <li>Products</li>
    <li>About Us</li>
    <li>Locations</li>
    <li>News</li>
    <li>Contact Us</li>
    <li>Online Store</li>
  </ul>
</nav>

<section class="hero abs"></section>
<div class="service-tile tile-packaging abs">
  <h2><svg class="tile-arrow" viewBox="0 0 14 14"><circle cx="7" cy="7" r="7" fill="#fff"/><path d="M5.5 4l3.5 3-3.5 3z" fill="#a8360a"/></svg>Packaging</h2>
  <p>BOXES, FILM &amp; SHIPPING GOODS</p>
  <span class="btn-small btn-light">Read More</span>
</div>
<div class="service-tile tile-printing abs">
  <h2><svg class="tile-arrow" viewBox="0 0 14 14"><circle cx="7" cy="7" r="7" fill="#fff"/><path d="M5.5 4l3.5 3-3.5 3z" fill="#d68e06"/></svg>Printing</h2>
  <p>FORMS, LABELS, SIGNAGE</p>
  <span class="btn-small btn-dark">Read More</span>
</div>
<div class="service-tile tile-distribution abs">
  <h2><svg class="tile-arrow" viewBox="0 0 14 14"><circle cx="7" cy="7" r="7" fill="#fff"/><path d="M5.5 4l3.5 3-3.5 3z" fill="#7c9e14"/></svg>Distribution</h2>
  <p>DELIVERED TO EVERY SITE</p>
  <span class="btn-small btn-dark">Read More</span>
</div>
<div class="hero-media abs" role="img" aria-label="Stacks of cardboard boxes in a warehouse"></div>
<div class="play-btn abs">PLAY</div>

<aside class="capabilities abs">
  <div class="panel-title">OUR CAPABILITIES</div>
  <ul class="cap-list">
    <li class="cap-item"><a href="#">Centralized pricing programs</a><p>One negotiated price list for every branch, office and store you operate, billed to one account.</p></li>
    <li class="cap-item"><a href="#">Budget controls by location</a><p>Set spending limits and approvals for each site from one easy dashboard.</p></li>
    <li class="cap-item"><a href="#">Company presentation (PPT)</a><p>Download our overview slides to share with your purchasing team.</p></li>
  </ul>
</aside>

<form class="newsletter abs">
  <h3>NEWSLETTER SIGN UP!</h3>
  <div class="newsletter-field"></div>
  <div class="newsletter-actions">
    <span class="btn-subscribe">Subscribe</span>
    <a class="unsubscribe" href="#">Unsubscribe</a>
  </div>
</form>

<h2 class="section-title intro-title abs">One supplier for every business location</h2>
<article class="feature feature-one abs">
  <div class="feature-media media-office" role="img" aria-label="Bright multi-site office building"></div>
  <div>
    <h4>Built for manufacturing and multi-site businesses</h4>
    <p>Banks, medical and dental offices, schools, retailers and plants rely on us for packaging, printed materials, office, janitorial and retail supplies, with pricing and controls set once for all sites.</p>
  </div>
</article>
<article class="feature feature-two abs">
  <div class="feature-media media-boxes" role="img" aria-label="Pallets of stacked cardboard boxes"></div>
  <div>
    <h4>Lower pricing for business accounts</h4>
    <p>Shop our full catalog at www.store.maplewickhaven.com and ask about business accounts. Registered companies get lower pricing, volume discounts and scheduled delivery.</p>
  </div>
</article>

<h2 class="section-title lines-title abs">Product lines for your business needs</h2>
<ul class="link-col col-a abs"><li><a href="#">Corrugated boxes &amp; mailers</a></li><li><a href="#">Stretch film &amp; tape</a></li><li><a href="#">Labels &amp; printed forms</a></li></ul>
<ul class="link-col col-b abs"><li><a href="#">Paper &amp; office supplies</a></li><li><a href="#">Breakroom &amp; food service</a></li><li><a href="#">Janitorial &amp; sanitation</a></li></ul>
<ul class="link-col col-c abs"><li><a href="#">Retail bags &amp; displays</a></li><li><a href="#">Signage &amp; promotional print</a></li><li><a href="#">Safety &amp; facility supplies</a></li></ul>

<footer class="site-footer abs"></footer>
<div class="footer-col footer-services abs">
  <h3>Best Services</h3>
  <ul class="service-list">
    <li>Custom packaging design</li>
    <li>Commercial printing</li>
    <li>Scheduled multi-site delivery</li>
    <li>Inventory management</li>
    <li>Budget reporting by site</li>
  </ul>
</div>
<div class="footer-col footer-standards abs">
  <h3>Our standards</h3>
  <p class="standards-lead">Service your locations can count on</p>
  <p class="standards-text">Accurate orders, dependable delivery windows and a dedicated account manager who knows your sites, budgets and products.</p>
  <span class="btn-read">Read more</span>
</div>
<div class="footer-col footer-social abs">
  <h3>Find us elsewhere:</h3>
  <ul class="social-list">
    <li>RSS SUBMIT<span class="social-square sq-orange"></span></li>
    <li>FOLLOW US ON CHIRPER<span class="social-square sq-blue"></span></li>
    <li>WANDERLINK<span class="social-square sq-green"></span></li>
  </ul>
</div>

<div class="bottom-bar abs"></div>
<p class="copyright abs">All Right Reserved 2015. Maplewick Haven supply.</p>
<ul class="footer-nav abs">
  <li class="is-active">Home</li>
  <li>Products</li>
  <li>Locations</li>
  <li>News</li>
  <li>Business pricing</li>
  <li>Contacts</li>
</ul>

</body>
</html>
```